SkyvornQ Business Cards and Stationary Design

Need a design for our business cards and stationary. I want to carry on the theme of the logo. I want the business cards to have a design on the back. I would like the business cards and the stationary to carry the same theme, design scheme, and branding

Target Market(s)

Airlines and Maintenance Facilities

Industry/Entity Type

Aviation

Contact Information for Business Card

Name
Position Title
Address: 4827 Trellis Hollow Road, Halvern Point, Solmara, 34951
Office Number
Mobile Number
Email
Website

Font styles to use
Serif
Sans Serif

Colors

Designer to choose colors to be used in the design.

```html
<!DOCTYPE html>
<html lang="en">
<head>
<meta charset="utf-8">
<title>SkyvornQ Business Card</title>
<link rel="stylesheet" href="https://fonts.googleapis.com/css2?family=Open+Sans:wght@400;700&display=swap">
<style>
  :root {
    --page-bg: #e9ebee;
    --blue-light: #0aa6e8;
    --blue-mid: #0a86cf;
    --blue-deep: #0b4a93;
    --white: #ffffff;
    --disc-light: #f7f8f9;
    --disc-shade: #dcdee2;
    --brand-navy: #183a6e;
  }
  * { margin: 0; padding: 0; box-sizing: border-box; }
  html, body {
    width: 1200px;
    height: 900px;
    overflow: hidden;
    background: var(--page-bg);
    font-family: "Open Sans", Arial, sans-serif;
  }
  .card {
    position: absolute;
    left: 150px;
    top: 170px;
    width: 900px;
    height: 559px;
    overflow: hidden;
    color: var(--white);
    background:
      radial-gradient(ellipse 70% 90% at 38% 40%, var(--blue-light) 0%, var(--blue-mid) 45%, var(--blue-deep) 100%);
    box-shadow: 0 10px 30px rgba(0, 0, 0, 0.18);
  }
  .holder {
    position: absolute;
    left: 50px;
    top: 62px;
  }
  .holder-name {
    font-size: 28px;
    font-weight: 700;
    letter-spacing: 0.3px;
    text-transform: uppercase;
    line-height: 1.2;
  }
  .holder-title {
    font-size: 25px;
    font-weight: 400;
    line-height: 1.3;
  }
  .contacts {
    position: absolute;
    left: 50px;
    top: 283px;
    list-style: none;
    font-size: 27px;
    line-height: 32px;
  }
  .contacts li {
    display: flex;
    align-items: center;
    gap: 8px;
  }
  .contacts svg {
    width: 20px;
    height: 20px;
    flex: none;
    fill: var(--white);
  }
  .address {
    position: absolute;
    left: 50px;
    top: 427px;
    font-size: 27px;
    line-height: 32px;
    font-style: normal;
  }
  .brand-disc {
    position: absolute;
    left: 392px;
    top: 49px;
    width: 460px;
    height: 460px;
    border-radius: 50%;
    background: radial-gradient(circle at 45% 40%, var(--disc-light) 0%, #eceef0 60%, var(--disc-shade) 100%);
    display: flex;
    flex-direction: column;
    align-items: center;
    justify-content: center;
    gap: 22px;
  }
  .brand-dot {
    width: 96px;
    height: 96px;
    border-radius: 50%;
    background: var(--brand-navy);
  }
  .brand-name {
    font-size: 40px;
    font-weight: 700;
    letter-spacing: 5px;
    color: var(--brand-navy);
    text-transform: uppercase;
  }
</style>
</head>
<body>
  <section class="card">
    <header class="holder">
      <h1 class="holder-name">Marcus Delaney</h1>
      <p class="holder-title">Managing Director</p>
    </header>

    <ul class="contacts">
      <li>
        <svg viewBox="0 0 20 20" aria-hidden="true"><path d="M2 7c0-2 3.5-3.5 8-3.5S18 5 18 7v1.5h-4V7.2c-1.2-.4-2.6-.6-4-.6s-2.8.2-4 .6v1.3H2zM4 10h12l1.5 7h-15z"/></svg>
        <span>044-555 218 640</span>
      </li>
      <li>
        <svg viewBox="0 0 20 20" aria-hidden="true"><path d="M6 1h8a1.5 1.5 0 0 1 1.5 1.5v15A1.5 1.5 0 0 1 14 19H6a1.5 1.5 0 0 1-1.5-1.5v-15A1.5 1.5 0 0 1 6 1zm.5 2.5v11h7v-11zM10 15.5a1 1 0 1 0 0 2 1 1 0 0 0 0-2z"/></svg>
        <span>044-555 218 640</span>
      </li>
      <li>
        <svg viewBox="0 0 20 20" aria-hidden="true"><path d="M2 5h16v10H2zm1.5 1.3v.4L10 11l6.5-4.3v-.4zm0 2.2v5h13v-5L10 12.8z"/></svg>
        <span>info@skyvornq.com</span>
      </li>
      <li>
        <svg viewBox="0 0 20 20" aria-hidden="true"><path d="M10 2a8 8 0 1 0 0 16 8 8 0 0 0 0-16zm0 1.6a6.4 6.4 0 0 1 5.8 3.7H12.5L11 5.5 8.6 7.2 9.8 9.6 8 12.2l1 3.9A6.4 6.4 0 0 1 4 6.2l2.2 1.3L7 5.2 6.4 4.6A6.4 6.4 0 0 1 10 3.6z"/></svg>
        <span>www.skyvornq.com</span>
      </li>
    </ul>

    <address class="address">
      4827 Trellis Hollow Road<br>
      Halvern Point, Solmara, 34951
    </address>

    <div class="brand-disc">
      <span class="brand-dot" aria-hidden="true"></span>
      <span class="brand-name">SkyvornQ</span>
    </div>
  </section>
</body>
</html>
```